Business Card Design for Varomir Facility Services

We are looking for a Business Card Design for the Company "Varomir Facility Services."
Front side:
- Company Logo (small)
- Company Name, address, pohone, website and personal data.
- white background, for text e.g. company colors (blue or green like in the logo)
Please use following data:
Company data:
Varomir Facility Services Kostelac
Birkenhaldweg 14
6330 Cham
www.varomir-fs.ch
Person data:
Tarik Kostelac
Geschäftsführer
+41 76 519 47 83
info@varomir-fs.ch
Back side:
could be colored in blue or green
please use a big logo sing and some smaller icons to say what is all beeing offered in facility services, like cleaning, maintenance cleaning
industrial cleaning, caretaking, gardening, disposal. There is no need for everyone of the icons if there are similar or an icon is standing for more of them.
colors to use:
blue: HEX 246BB0
green: HEX 52B33E

```html
<!DOCTYPE html>
<html lang="de">
<head>
<meta charset="utf-8">
<title>Varomir Facility Services – Visitenkarte</title>
<link rel="stylesheet" href="https://fonts.googleapis.com/css2?family=Roboto:wght@400;500;700;900&display=swap">
<style>
  :root {
    --brand-blue: #246bb0;
    --brand-green: #52b33e;
    --card-green: #1aa83a;
    --ink: #1d1d1d;
    --paper: #ffffff;
    --stage: #d9d9d9;
  }
  * { box-sizing: border-box; margin: 0; padding: 0; }
  html, body { width: 1200px; height: 1200px; overflow: hidden; }
  body {
    background: var(--stage);
    font-family: "Roboto", Arial, sans-serif;
    display: flex; flex-direction: column; align-items: center;
    padding-top: 45px; gap: 30px;
  }
  .card {
    width: 880px; height: 540px; border-radius: 28px;
    position: relative; overflow: hidden;
    box-shadow: 0 6px 18px rgba(0,0,0,.18);
  }

  /* back side */
  .card-back { background: var(--card-green); color: var(--paper); }
  .back-brand {
    position: absolute; top: 110px; left: 0; right: 0;
    display: flex; align-items: center; justify-content: center; gap: 22px;
  }
  .brand-dot { width: 54px; height: 54px; border-radius: 50%; background: var(--paper); }
  .back-brand .brand-name {
    font-weight: 700; font-size: 52px; letter-spacing: 1px; line-height: 1.05;
  }
  .services {
    position: absolute; top: 300px; left: 0; right: 0;
    display: flex; justify-content: center; gap: 60px;
  }
  .service { width: 130px; display: flex; flex-direction: column; align-items: center; gap: 12px; }
  .service-badge {
    width: 110px; height: 110px; border-radius: 50%;
    border: 3px solid var(--paper); padding: 6px;
  }
  .service-badge .badge-art {
    width: 100%; height: 100%; border-radius: 50%; background: #bfe8c6;
  }
  .service-label {
    font-weight: 700; font-size: 15px; text-transform: uppercase;
    text-align: center; line-height: 1.1; letter-spacing: .3px;
  }

  /* front side */
  .card-front { background: var(--paper); }
  .front-brand {
    position: absolute; top: 70px; left: 70px;
    display: flex; align-items: center; gap: 16px;
  }
  .front-brand .brand-dot { width: 46px; height: 46px; background: var(--brand-blue); }
  .front-brand .brand-name {
    font-weight: 700; font-size: 40px; color: var(--brand-blue);
  }
  .contact-block {
    position: absolute; left: 110px; bottom: 75px;
    display: flex; align-items: stretch; gap: 26px;
  }
  .person { text-align: right; align-self: center; }
  .person-name { color: var(--brand-blue); font-weight: 700; font-size: 32px; }
  .person-role { color: var(--ink); font-size: 20px; margin-top: 4px; }
  .divider { width: 2px; background: var(--brand-green); }
  .company-name { color: var(--brand-green); font-weight: 700; font-size: 22px; }
  .company-address { color: var(--ink); font-size: 21px; margin: 4px 0 10px; }
  .contact-list { list-style: none; }
  .contact-list li {
    display: flex; align-items: center; gap: 12px;
    color: var(--ink); font-size: 21px; line-height: 1.45;
  }
  .contact-list svg { width: 20px; height: 20px; flex: none; }
  .web-strong { color: var(--brand-blue); font-weight: 500; }
</style>
</head>
<body>

  <section class="card card-back" aria-label="Rückseite">
    <div class="back-brand">
      <span class="brand-dot"></span>
      <span class="brand-name">Varomir<br>Facility Services</span>
    </div>
    <div class="services">
      <div class="service">
        <div class="service-badge"><div class="badge-art" role="img" aria-label="Symbol Unterhaltsreinigung: Eimer mit Pinsel"></div></div>
        <div class="service-label">Maintenance<br>Cleaning</div>
      </div>
      <div class="service">
        <div class="service-badge"><div class="badge-art" role="img" aria-label="Symbol Hauswartung: Handschlag im Herz"></div></div>
        <div class="service-label">Caretaking</div>
      </div>
      <div class="service">
        <div class="service-badge"><div class="badge-art" role="img" aria-label="Symbol Gartenpflege: Blume im Topf"></div></div>
        <div class="service-label">Gardening</div>
      </div>
      <div class="service">
        <div class="service-badge"><div class="badge-art" role="img" aria-label="Symbol Entsorgung: Mülleimer"></div></div>
        <div class="service-label">Disposal</div>
      </div>
    </div>
  </section>

  <section class="card card-front" aria-label="Vorderseite">
    <div class="front-brand">
      <span class="brand-dot"></span>
      <span class="brand-name">Varomir Facility Services</span>
    </div>
    <div class="contact-block">
      <div class="person">
        <div class="person-name">Tarik Kostelac</div>
        <div class="person-role">Geschäftsführer</div>
      </div>
      <div class="divider"></div>
      <div class="company">
        <div class="company-name">Varomir Facility Services Kostelac</div>
        <div class="company-address">Birkenhaldweg 14, 6330 Cham</div>
        <ul class="contact-list">
          <li>
            <svg viewBox="0 0 24 24" aria-hidden="true"><path fill="#246bb0" d="M6.6 10.8a15.1 15.1 0 0 0 6.6 6.6l2.2-2.2a1 1 0 0 1 1-.25 11.4 11.4 0 0 0 3.6.57 1 1 0 0 1 1 1V20a1 1 0 0 1-1 1A17 17 0 0 1 3 4a1 1 0 0 1 1-1h3.5a1 1 0 0 1 1 1c0 1.25.2 2.45.57 3.57a1 1 0 0 1-.25 1z"/></svg>
            +41 76 519 47 83
          </li>
          <li>
            <svg viewBox="0 0 24 24" aria-hidden="true"><rect x="2" y="5" width="20" height="14" rx="2" fill="#246bb0"/><path d="M3 6l9 7 9-7" fill="none" stroke="#fff" stroke-width="1.6"/></svg>
            info@varomir-fs.ch
          </li>
          <li>
            <svg viewBox="0 0 24 24" aria-hidden="true"><g fill="none" stroke="#246bb0" stroke-width="1.8"><circle cx="12" cy="12" r="9.5"/><ellipse cx="12" cy="12" rx="4.2" ry="9.5"/><path d="M2.5 12h19M4 7h16M4 17h16"/></g></svg>
            <span>www.<span class="web-strong">varomir-fs</span>.ch</span>
          </li>
        </ul>
      </div>
    </div>
  </section>

</body>
</html>
```